BRIGHT RIVER POWER.

I'd like my business logo.
contact name: Dennis Halvorsen
phone:0438759164
email: info@brightriverpower.net.au
website: www.brightriverpower.net.au

services:
solar
battery storage
LED lighting
energy saving solutions
general electrical
I'd like the design to look professional

Target Market(s)

Everyone

Industry/Entity Type

Business

Contact Information for Business Card

as described above

Requirements
Must have
• Id like the colours and the design to work well with my logo.

```html
<!DOCTYPE html>
<html lang="en">
<head>
<meta charset="utf-8">
<title>Bright River Power – Business Card</title>
<link rel="stylesheet" href="https://fonts.googleapis.com/css2?family=Montserrat:wght@400;500;700;800&display=swap">
<style>
  :root {
    --page: #e9e6e1;
    --card-black: #0c0c0c;
    --card-white: #fbfbfa;
    --green: #7cc242;
    --green-light: #a8d86b;
    --orange: #f39a1f;
    --text-light: #f2f2f2;
  }
  html, body {
    margin: 0;
    width: 1200px;
    height: 1022px;
    overflow: hidden;
    background: var(--page);
    font-family: "Montserrat", sans-serif;
  }
  .card {
    position: absolute;
    left: 100px;
    top: 225px;
    width: 1000px;
    height: 571px;
    border-radius: 26px;
    overflow: hidden;
    background: var(--card-black);
    box-shadow: 0 10px 30px rgba(0,0,0,0.18);
  }
  .card-bg {
    position: absolute;
    inset: 0;
  }
  .brand-panel {
    position: absolute;
    left: 40px;
    top: 0;
    width: 380px;
    height: 571px;
    display: flex;
    align-items: center;
    justify-content: center;
    gap: 22px;
  }
  .brand-dot {
    width: 46px;
    height: 46px;
    border-radius: 50%;
    background: var(--orange);
    flex: none;
  }
  .brand-name-large {
    font-weight: 800;
    font-size: 40px;
    line-height: 1.1;
    color: var(--green);
    letter-spacing: 1px;
  }
  .details {
    position: absolute;
    right: 48px;
    top: 50px;
    width: 440px;
    text-align: right;
    color: var(--text-light);
  }
  .brand-row {
    display: flex;
    justify-content: flex-end;
    align-items: center;
    gap: 14px;
    margin-bottom: 26px;
  }
  .brand-dot-small {
    width: 26px;
    height: 26px;
    border-radius: 50%;
    background: var(--orange);
  }
  .brand-name {
    font-weight: 700;
    font-size: 30px;
    color: var(--green);
    letter-spacing: 0.5px;
  }
  .contact-name {
    font-weight: 700;
    font-size: 31px;
    color: var(--orange);
    margin: 0 0 12px;
  }
  .contact-line {
    display: flex;
    justify-content: flex-end;
    align-items: center;
    gap: 12px;
    font-size: 20px;
    font-weight: 400;
    margin: 6px 0;
  }
  .contact-line .icon {
    width: 18px;
    height: 18px;
    flex: none;
  }
  .web { color: var(--orange); }
  .services {
    list-style: none;
    margin: 30px 0 0;
    padding: 0;
  }
  .services li {
    display: flex;
    justify-content: flex-end;
    align-items: center;
    gap: 14px;
    font-size: 21px;
    margin: 8px 0;
  }
  .services li::after {
    content: "";
    width: 9px;
    height: 9px;
    border-radius: 50%;
    background: var(--orange);
    margin-right: 4px;
  }
</style>
</head>
<body>
  <section class="card" aria-label="Bright River Power business card">
    <svg class="card-bg" viewBox="0 0 1000 571" width="1000" height="571" aria-hidden="true">
      <defs>
        <linearGradient id="band" x1="0" y1="0" x2="0" y2="1">
          <stop offset="0" stop-color="var(--green-light)"/>
          <stop offset="1" stop-color="var(--green)"/>
        </linearGradient>
      </defs>
      <path d="M0,0 L420,0 Q600,285 420,571 L0,571 Z" fill="url(#band)"/>
      <path d="M0,0 L400,0 Q572,285 400,571 L0,571 Z" fill="var(--card-black)"/>
      <path d="M0,0 L392,0 Q562,285 392,571 L0,571 Z" fill="var(--card-white)"/>
    </svg>

    <div class="brand-panel">
      <span class="brand-dot"></span>
      <div class="brand-name-large">BRIGHT<br>RIVER<br>POWER</div>
    </div>

    <div class="details">
      <div class="brand-row">
        <span class="brand-dot-small"></span>
        <span class="brand-name">BRIGHT RIVER POWER</span>
      </div>
      <p class="contact-name">Dennis Halvorsen</p>
      <div class="contact-line">
        <span>0438759164</span>
        <svg class="icon" viewBox="0 0 24 24"><path d="M6.6 10.8a15 15 0 0 0 6.6 6.6l2.2-2.2a1 1 0 0 1 1-.25 11.4 11.4 0 0 0 3.6.57 1 1 0 0 1 1 1V20a1 1 0 0 1-1 1A17 17 0 0 1 3 4a1 1 0 0 1 1-1h3.5a1 1 0 0 1 1 1c0 1.25.2 2.45.57 3.57a1 1 0 0 1-.25 1z" fill="var(--orange)"/></svg>
      </div>
      <div class="contact-line">
        <span>info@brightriverpower.net.au</span>
        <svg class="icon" viewBox="0 0 24 24"><rect x="3" y="5" width="18" height="14" rx="2" fill="none" stroke="var(--orange)" stroke-width="2"/><path d="M3 7l9 6 9-6" fill="none" stroke="var(--orange)" stroke-width="2"/></svg>
      </div>
      <div class="contact-line">
        <span class="web">www.brightriverpower.net.au</span>
        <svg class="icon" viewBox="0 0 24 24"><circle cx="12" cy="12" r="9" fill="none" stroke="var(--orange)" stroke-width="2"/><path d="M3 12h18M12 3c3 3 3 15 0 18M12 3c-3 3-3 15 0 18" fill="none" stroke="var(--orange)" stroke-width="1.6"/></svg>
      </div>
      <ul class="services">
        <li>Solar</li>
        <li>Battery storage</li>
        <li>LED lighting</li>
        <li>Energy saving solutions</li>
      </ul>
    </div>
  </section>
</body>
</html>
```